Velundra Jobs portal

Velundra Jobs is a job portal connecting job seekers and companies offering part time jobs in the Mena region, starting in the UAE. We would like to see designs that use the color blue. We have attached images to give an idea what the website should look like. When a company posts a job the job seekers are not allowed to see which company has posted a job. There should also be a coinvex gateway. On the landing page we want a catching picture that we will send.

Target Market(s)

Students and promotional workers

Logo Text

Velundra Jobs

Coding

Coded - Design and coding required

Number of Pages Required

4 page

Font styles to use
Sans Serif

Colors
33a6d7
0692cd
85cae6

```html
<!DOCTYPE html>
<html lang="en">
<head>
<meta charset="utf-8">
<title>Velundra Jobs – Job listings</title>
<link href="https://fonts.googleapis.com/css2?family=Catamaran:wght@400;500;600;700&family=Open+Sans:wght@400&display=swap" rel="stylesheet">
<style>
:root{
  --blue-top:#1fb0f5;
  --blue-bottom:#2a78cf;
  --blue-title:#2f7ac8;
  --teal:#4fc6c6;
  --purple-top:#8a3ea8;
  --purple-bottom:#5c2a84;
  --logout:#d80a0a;
  --text:#555;
  --line:#d5d5d5;
  --panel:#f2f2f2;
  --cream:#fffdf6;
  --white:#fff;
}
*{box-sizing:border-box;margin:0;padding:0}
html,body{width:1200px;height:831px;overflow:hidden;background:var(--white)}
body{position:relative;font-family:"Catamaran",sans-serif;color:var(--text)}
.site-header{position:absolute;left:0;top:0;width:1200px;height:78px;background:linear-gradient(var(--blue-top),var(--blue-bottom))}
.logo{position:absolute;left:99px;top:10px;color:var(--white);font-size:40px;font-weight:400;letter-spacing:.5px;line-height:1}
.main-nav a{position:absolute;top:27px;color:var(--white);font-size:14px;font-weight:500;text-decoration:none}
.header-icon{position:absolute;top:24px}
.avatar{position:absolute;left:948px;top:12px;width:44px;height:44px;border-radius:50%;background:radial-gradient(#d9b49a,#8d7a6a);border:2px solid #e8e8e8}
.logout{position:absolute;left:1016px;top:15px;width:84px;height:40px;border-radius:3px;background:var(--logout);color:var(--white);font-weight:700;font-size:15px;display:flex;align-items:center;justify-content:center}
.mascot{position:absolute;left:0;top:460px;width:285px;height:308px;background:radial-gradient(ellipse at 45% 30%,rgba(133,202,230,.28),rgba(133,202,230,.1) 55%,rgba(255,255,255,0) 75%)}
.categories{position:absolute;left:99px;top:106px;width:182px;height:322px;background:linear-gradient(90deg,var(--panel),#fbfbfb);border-radius:3px;font-family:"Open Sans",sans-serif;font-size:12.5px;color:#555;list-style:none;padding-top:17px}
.categories li{height:31px;padding-left:17px;position:relative}
.categories .count{position:absolute;left:136px}
.filter-bar{position:absolute;left:297px;top:106px;width:804px;height:78px;border:1px solid var(--line);border-radius:3px;background:linear-gradient(#fff,#f1f1f1)}
.field{position:absolute;top:15px;height:45px;border:1px solid var(--line);border-radius:10px;background:var(--white);font-size:12.5px;color:#666;padding:15px 0 0 12px}
.field.keyword{left:17px;width:278px}
.field.district{left:310px;width:278px;padding-left:15px}
.field.district svg{position:absolute;right:15px;top:20px}
.filter-btn{position:absolute;left:615px;top:12px;width:159px;height:50px;border-radius:3px;background:linear-gradient(var(--purple-top),var(--purple-bottom));color:var(--white);font-size:18px;font-weight:700;display:flex;align-items:center;justify-content:center}
.jobs{position:absolute;left:299px;top:203px;width:801px;border-collapse:collapse;border:1px solid #ddd}
.jobs th{height:58px;background:linear-gradient(var(--blue-top),var(--blue-bottom));color:var(--white);font-size:23px;font-weight:700;text-align:left;border-left:1px solid #1d5fa8;padding-left:28px}
.jobs th:first-child{border-left:0;padding-left:28px}
.jobs td{font-size:14.5px;color:#666;border-left:1px solid #ccc;padding-left:26px}
.jobs td:first-child{border-left:0}
.jobs td.action{padding-left:37px}
.jobs tr.highlight td{background:var(--teal);color:var(--white);height:60px}
.jobs tr.row td{height:61px}
.jobs tr.cream td{background:var(--cream)}
.apply{width:125px;height:40px;border-radius:3px;color:var(--white);font-size:17px;font-weight:700;display:flex;align-items:center;justify-content:center;background:linear-gradient(var(--blue-top),var(--blue-bottom))}
.highlight .apply{background:linear-gradient(var(--purple-top),var(--purple-bottom))}
.featured-title{position:absolute;left:298px;top:526px;color:var(--blue-title);font-size:22px;font-weight:700}
.provider{position:absolute;top:578px;width:146px;height:154px}
.site-footer{position:absolute;left:0;top:768px;width:1200px;height:63px;background:linear-gradient(var(--blue-top),var(--blue-bottom));color:var(--white);font-size:12.5px;font-weight:500}
.site-footer .copy{position:absolute;left:99px;top:24px}
.site-footer .links{position:absolute;right:97px;top:22px}
</style>
</head>
<body>
<header class="site-header">
  <div class="logo">velundra</div>
  <nav class="main-nav">
    <a href="#" style="left:419px">ABOUT US</a>
    <a href="#" style="left:522px">CONTACT US</a>
  </nav>
  <svg class="header-icon" style="left:870px" width="20" height="20" viewBox="0 0 20 20"><circle cx="8" cy="8" r="6" fill="none" stroke="#fff" stroke-width="2.6"/><line x1="12.5" y1="12.5" x2="18" y2="18" stroke="#fff" stroke-width="3" stroke-linecap="round"/></svg>
  <svg class="header-icon" style="left:911px" width="20" height="21" viewBox="0 0 20 21"><path d="M4 15V9a6 6 0 0 1 12 0v6l2 2H2z" fill="none" stroke="#fff" stroke-width="1.6" stroke-linejoin="round"/><path d="M8 18.5a2 2 0 0 0 4 0" fill="none" stroke="#fff" stroke-width="1.6"/></svg>
  <div class="avatar" role="img" aria-label="User profile photo"></div>
  <div class="logout">LOGOUT</div>
</header>

<div class="mascot" role="img" aria-label="Faint background illustration of the brand mascot"></div>

<ul class="categories">
  <li>Category 1<span class="count">(33)</span></li>
  <li>Category 2<span class="count">(3)</span></li>
  <li>Category 3<span class="count">(23)</span></li>
  <li>Category 4<span class="count">(13)</span></li>
  <li>Category 5<span class="count">(43)</span></li>
  <li>Category 6<span class="count">(13)</span></li>
  <li>Category 7<span class="count">(189)</span></li>
  <li>Category 8<span class="count">(43)</span></li>
  <li>Category 9<span class="count">(983)</span></li>
  <li>Category 10<span class="count">(23)</span></li>
</ul>

<div class="filter-bar">
  <div class="field keyword">KEY WORD</div>
  <div class="field district">DISTRICT<svg width="9" height="5" viewBox="0 0 9 5"><path d="M0 0h9L4.5 5z" fill="#333"/></svg></div>
  <div class="filter-btn">FILTER JOBS</div>
</div>

<table class="jobs">
  <colgroup><col style="width:169px"><col style="width:180px"><col style="width:257px"><col></colgroup>
  <tr><th>JOB TITLE</th><th style="padding-left:22px">DUE DATE</th><th style="padding-left:22px">PROVIDER NAME</th><th></th></tr>
  <tr class="highlight"><td>Job title number 1</td><td>Due date 23 jan 2015</td><td>Provider1</td><td class="action"><div class="apply">APPLY NOW</div></td></tr>
  <tr class="row"><td>Job title number 1</td><td>Due date 23 jan 2015</td><td>Provider1</td><td class="action"><div class="apply">APPLY NOW</div></td></tr>
  <tr class="row cream"><td>Job title number 1</td><td>Due date 23 jan 2015</td><td>Provider1</td><td class="action"><div class="apply">APPLY NOW</div></td></tr>
  <tr class="row"><td>Job title number 1</td><td>Due date 23 jan 2015</td><td>Provider1</td><td class="action"><div class="apply">APPLY NOW</div></td></tr>
</table>

<h2 class="featured-title">FEATURED JOB PROVIDERS</h2>
<div class="provider" style="left:297px;background:linear-gradient(135deg,#d9b8a0,#6b5a50)" role="img" aria-label="Portrait photo of a job provider"></div>
<div class="provider" style="left:459px;background:linear-gradient(160deg,#e8d6c4,#3a3a40)" role="img" aria-label="Portrait photo of a job provider"></div>
<div class="provider" style="left:626px;background:linear-gradient(160deg,#cfd4d8,#3b3f4a)" role="img" aria-label="Portrait photo of a job provider"></div>
<div class="provider" style="left:790px;background:linear-gradient(160deg,#e6e8ea,#c9b9a8)" role="img" aria-label="Portrait photo of a job provider"></div>
<div class="provider" style="left:956px;background:linear-gradient(160deg,#dfe2e4,#c8a894)" role="img" aria-label="Portrait photo of a job provider"></div>

<footer class="site-footer">
  <div class="copy">Copyrights reserved to Velundra 2015</div>
  <div class="links">About us - terms and conditionsv sitemap</div>
</footer>
</body>
</html>
```